Business Card Design for company

We want new business cards. We'd like something different-- yet still highly professional. Our tagline is Providing leadership, delivering success. Stock photos are ok, as long as they are relevant and look upscale.

Target Market(s)

Architecture/Business Management Consulting/Engineering Consulting

Contact Information for Business Card

dark gray background with pops of blue might be good, but you tell me. You're the designers. Rounded corners might be nice, but again, you tell me.

Font styles to use
Serif
Sans Serif

Colors
3276b5
5c5c5c
9d9d9d
fbfbfb

Requirements
Nice to have
• Something different, but still very professional.

```html
<!DOCTYPE html>
<html lang="en">
<head>
<meta charset="utf-8">
<title>Halvern Partners – Business Cards</title>
<link href="https://fonts.googleapis.com/css2?family=Open+Sans:wght@400;600&display=swap" rel="stylesheet">
<style>
  :root {
    --backdrop: #3a3330;
    --card: #1e2226;
    --blue: #3276b5;
    --white: #fbfbfb;
    --silver: #d6d6d6;
    --grey: #9d9d9d;
  }
  * { margin: 0; padding: 0; box-sizing: border-box; }
  html, body { width: 1200px; height: 864px; overflow: hidden; }
  body {
    background: var(--backdrop);
    font-family: "Open Sans", sans-serif;
    position: relative;
  }
  .card {
    position: absolute;
    width: 540px;
    height: 309px;
    background: var(--card);
    border-radius: 4px;
  }
  .card-front { left: 50px; top: 110px; }
  .card-back { left: 610px; top: 445px; }

  .front-brand {
    position: absolute;
    left: 0; right: 0; top: 100px;
    text-align: center;
    color: var(--silver);
    font-weight: 600;
    font-size: 38px;
    letter-spacing: 2px;
    text-transform: uppercase;
  }
  .front-tagline {
    position: absolute;
    left: 0; right: 0; top: 178px;
    text-align: center;
    color: var(--white);
    font-size: 15px;
  }
  .front-tagline .dot { margin: 0 8px; }

  .back-brand {
    position: absolute;
    right: 34px; top: 52px;
    color: var(--blue);
    font-weight: 600;
    font-size: 30px;
    letter-spacing: 1.5px;
    text-transform: uppercase;
    text-align: right;
    line-height: 1.1;
  }
  .person { position: absolute; left: 34px; top: 40px; }
  .person-name {
    color: var(--blue);
    font-weight: 600;
    font-size: 18px;
    text-transform: uppercase;
    line-height: 1.1;
  }
  .person-role {
    color: var(--white);
    font-size: 14px;
    text-transform: uppercase;
    line-height: 1.2;
  }
  .contacts {
    position: absolute;
    left: 34px; top: 92px;
    list-style: none;
    color: var(--white);
    font-size: 14px;
    line-height: 21px;
  }
  .contacts li { display: flex; align-items: center; gap: 9px; }
  .contacts svg { width: 12px; height: 12px; fill: var(--blue); flex: none; }
  .divider {
    position: absolute;
    left: 34px; right: 34px; top: 205px;
    height: 1px;
    background: var(--white);
  }
  .address {
    position: absolute;
    right: 34px; top: 218px;
    text-align: right;
    color: var(--white);
    font-size: 15px;
    line-height: 20px;
  }
</style>
</head>
<body>
  <section class="card card-front">
    <div class="front-brand">Halvern Partners</div>
    <p class="front-tagline">Providing leadership<span class="dot">•</span>delivering success</p>
  </section>

  <section class="card card-back">
    <div class="person">
      <div class="person-name">Daniel Marsh</div>
      <div class="person-role">President</div>
    </div>
    <ul class="contacts">
      <li>
        <svg viewBox="0 0 12 12" aria-hidden="true"><path d="M1 4c0-2 2-3 5-3s5 1 5 3l-2 1-1-2H4L3 5zM2 6h8l1 5H1z"/></svg>
        555 0142 7781
      </li>
      <li>
        <svg viewBox="0 0 12 12" aria-hidden="true"><path d="M3 0h6v12H3zM4 1.5v8h4v-8z"/></svg>
        555 0198 3364
      </li>
      <li>
        <svg viewBox="0 0 12 12" aria-hidden="true"><path d="M3 0h6v4H3zM1 4h10v6H1zM3 9h6v3H3z"/></svg>
        555 0127 4590
      </li>
      <li>
        <svg viewBox="0 0 12 12" aria-hidden="true"><path d="M0 2h12v8H0zM1 3l5 4 5-4z" fill-rule="evenodd"/></svg>
        daniel@halvernpartners.com
      </li>
    </ul>
    <div class="back-brand">Halvern<br>Partners</div>
    <div class="divider"></div>
    <address class="address" style="font-style:normal">
      4120 Linden Avenue<br>
      Oak Hollow, NY 11000<br>
      www.halvernpartners.com
    </address>
  </section>
</body>
</html>
```